Tolbek cards

I want a simple business card that pops.
Logo on one side.
On side two i want.
"Are you thinking about a new building on your property, or renovating an existing structure? Contact".....
Owners Name: Dale Whitacre
Owners Phone number: 610-555-0187
Address:4076 Copper Ridge RD, Hollins Ford, PA 16874
Committed to Quality, Service, and Integrity

```html
<!DOCTYPE html>
<html lang="en">
<head>
<meta charset="utf-8">
<title>Tolbek Builders LLC – Business Card</title>
<link rel="stylesheet" href="https://fonts.googleapis.com/css2?family=Poppins:wght@400;500;600;700&display=swap">
<style>
  :root {
    --stage: #1e1e21;
    --brown: #432f1d;
    --brown-text: #3b2818;
    --paper: #ffffff;
    --ink: #2a2a2a;
    --rule: #8a6a4c;
  }
  * { margin: 0; padding: 0; box-sizing: border-box; }
  html, body { width: 1200px; height: 800px; overflow: hidden; }
  body {
    background: var(--stage);
    font-family: "Poppins", sans-serif;
    display: flex;
    align-items: center;
    justify-content: center;
    gap: 40px;
  }
  .card {
    width: 560px;
    height: 320px;
    border-radius: 22px;
    position: relative;
    overflow: hidden;
  }
  .card--front {
    background: var(--brown);
    display: flex;
    align-items: center;
    justify-content: center;
  }
  .brand {
    display: flex;
    align-items: center;
    gap: 14px;
    font-weight: 700;
    text-transform: uppercase;
    line-height: 1;
  }
  .brand__mark { width: 26px; height: 26px; flex: none; }
  .card--front .brand { color: var(--paper); font-size: 40px; }
  .card--front .brand__mark { background: var(--paper); }

  .card--back { background: var(--paper); color: var(--ink); }
  .card--back .brand {
    position: absolute;
    left: 36px;
    top: 96px;
    width: 220px;
    flex-wrap: wrap;
    color: var(--brown-text);
    font-size: 28px;
  }
  .card--back .brand__mark { width: 20px; height: 20px; background: var(--brown-text); }
  .divider {
    position: absolute;
    left: 278px;
    top: 40px;
    width: 1px;
    height: 160px;
    background: var(--rule);
  }
  .contact {
    position: absolute;
    left: 300px;
    top: 40px;
    right: 24px;
  }
  .contact__name { font-size: 26px; font-weight: 700; color: var(--brown-text); line-height: 1.1; }
  .contact__role { font-size: 12px; font-weight: 600; margin-bottom: 12px; }
  .contact__tagline { font-size: 12px; line-height: 1.45; margin-bottom: 12px; }
  .contact__row {
    display: flex;
    align-items: flex-start;
    gap: 8px;
    font-size: 12px;
    line-height: 1.45;
  }
  .contact__row svg { width: 12px; height: 12px; flex: none; margin-top: 3px; }
  .pitch {
    position: absolute;
    left: 30px;
    right: 30px;
    bottom: 30px;
    text-align: center;
    font-size: 14px;
    line-height: 1.5;
  }
</style>
</head>
<body>
  <section class="card card--front">
    <div class="brand"><span class="brand__mark"></span>Tolbek Builders LLC</div>
  </section>

  <section class="card card--back">
    <div class="brand"><span class="brand__mark"></span>Tolbek Builders LLC</div>
    <div class="divider"></div>
    <div class="contact">
      <h1 class="contact__name">Dale Whitacre</h1>
      <p class="contact__role">Owners</p>
      <p class="contact__tagline">Committed to Quality,<br>Service, and Integrity</p>
      <p class="contact__row">
        <svg viewBox="0 0 24 24" aria-hidden="true"><path fill="#2a2a2a" d="M6.6 10.8a15 15 0 0 0 6.6 6.6l2.2-2.2a1 1 0 0 1 1-.25 11.4 11.4 0 0 0 3.6.57 1 1 0 0 1 1 1V20a1 1 0 0 1-1 1A17 17 0 0 1 3 4a1 1 0 0 1 1-1h3.5a1 1 0 0 1 1 1c0 1.25.2 2.45.57 3.57a1 1 0 0 1-.25 1z"/></svg>
        610-555-0187
      </p>
      <p class="contact__row">
        <svg viewBox="0 0 24 24" aria-hidden="true"><path fill="#2a2a2a" d="M12 2a7 7 0 0 0-7 7c0 5.25 7 13 7 13s7-7.75 7-13a7 7 0 0 0-7-7zm0 9.5A2.5 2.5 0 1 1 12 6.5a2.5 2.5 0 0 1 0 5z"/></svg>
        4076 Copper Ridge RD, Hollins Ford,<br>PA 16874
      </p>
    </div>
    <p class="pitch">"Are you thinking about a new building on your property,<br>or renovating an existing structure? Contact" .....</p>
  </section>
</body>
</html>
```